Business card design Needed for new logo / Construction business, home extensions and new builds

We need a business card design using our new logo files which i will attach to this project :)

We are a small construction business specialising in home extensions, new builds and property development. We are very ambitious and would appreciate professional and elegant designs for our new business card.

Very serious about using the services on MakerQuarry and recently acquired our new logo from here :)

Please get involved, i will feedback when i can as i am very busy but can respond daily, thanks

Target Market(s)

People that want to build onto their houses, new building developments or adding too their existing property

Industry/Entity Type

Construction

Contact Information for Business Card

Renwick Tolliver Construction, Lionel Ashby (Managing Director), Tel 07822254961, email - info@renwick-tolliver, www.renwick-tolliver.co.uk

Colors

Designer to choose colors to be used in the design.

Requirements
Must have
• I like a deep grey on the back please. A lot of you have provided black from and back, try mixing things up a little. The black looks cool 😎 Thanks

```html
<!DOCTYPE html>
<html lang="en">
<head>
<meta charset="utf-8">
<title>Renwick Tolliver Construction – Business Card</title>
<link rel="stylesheet" href="https://fonts.googleapis.com/css2?family=Montserrat:wght@400;500;600;700&display=swap">
<style>
  :root {
    --stage: #4a4a4c;
    --card-black: #0c0c0c;
    --deep-grey: #2e2f31;
    --grey-light: #3a3b3e;
    --grey-dark: #242527;
    --gold: #e0a92a;
    --gold-dark: #b98414;
    --white: #f4f4f4;
    --ink: #141414;
  }
  * { margin: 0; padding: 0; box-sizing: border-box; }
  html, body {
    width: 1200px; height: 689px; overflow: hidden;
    background: var(--stage);
    font-family: "Montserrat", Arial, sans-serif;
  }
  .canvas {
    position: relative; width: 1200px; height: 689px;
    display: flex; align-items: center; justify-content: center; gap: 60px;
  }
  .card {
    position: relative; width: 520px; height: 297px;
    border-radius: 18px; overflow: hidden;
    box-shadow: 0 18px 40px rgba(0,0,0,.45);
  }

  /* Brand side – deep grey */
  .card--brand { background: var(--deep-grey); }
  .brand-texture {
    position: absolute; inset: 0;
    background: linear-gradient(135deg, var(--grey-light) 0%, var(--grey-dark) 55%, var(--grey-light) 100%);
  }
  .brand-lockup {
    position: absolute; inset: 0;
    display: flex; flex-direction: column; align-items: center; justify-content: center; gap: 14px;
  }
  .brand-mark { width: 34px; height: 34px; background: var(--gold); }
  .brand-name {
    font-weight: 600; color: var(--gold);
    text-align: center; letter-spacing: 3px; line-height: 1.35;
    text-transform: uppercase;
  }
  .card--brand .brand-name { font-size: 25px; }

  /* Contact side */
  .card--contact { background: var(--card-black); }
  .card--contact .brand-lockup {
    inset: 26px 0 auto 0; height: 120px; gap: 10px;
  }
  .card--contact .brand-mark { width: 24px; height: 24px; }
  .card--contact .brand-name { font-size: 17px; letter-spacing: 2.5px; }

  .details {
    position: absolute; left: 0; right: 0; top: 160px;
    display: flex; justify-content: center; align-items: center;
  }
  .person { text-align: right; padding-right: 18px; }
  .person__name {
    font-weight: 700; font-size: 20px; color: var(--gold);
    letter-spacing: .5px; text-transform: uppercase;
  }
  .person__role { font-size: 12px; color: var(--white); margin-top: 3px; }
  .divider { width: 1px; height: 60px; background: var(--gold); }
  .contacts { list-style: none; padding-left: 18px; }
  .contacts li {
    display: flex; align-items: center; gap: 8px;
    font-size: 11.5px; color: var(--white); line-height: 19px;
  }
  .contacts svg { width: 11px; height: 11px; fill: var(--gold); flex: none; }

  .address-band {
    position: absolute; left: 0; right: 0; bottom: 22px; height: 30px;
    background: linear-gradient(90deg, var(--gold-dark), var(--gold) 40%, var(--gold-dark));
    display: flex; align-items: center; justify-content: center;
    font-size: 12px; font-weight: 500; color: var(--ink);
  }
  .address-rule {
    position: absolute; left: 0; right: 0; bottom: 12px; height: 1px; background: var(--gold-dark);
  }
</style>
</head>
<body>
<main class="canvas">

  <section class="card card--brand" aria-label="Business card, brand side">
    <div class="brand-texture" role="img" aria-label="Embossed tonal pattern of repeated brand marks"></div>
    <div class="brand-lockup">
      <div class="brand-mark"></div>
      <p class="brand-name">Renwick Tolliver<br>Construction</p>
    </div>
  </section>

  <section class="card card--contact" aria-label="Business card, contact side">
    <div class="brand-lockup">
      <div class="brand-mark"></div>
      <p class="brand-name">Renwick Tolliver<br>Construction</p>
    </div>

    <div class="details">
      <div class="person">
        <p class="person__name">Lionel Ashby</p>
        <p class="person__role">Managing Director</p>
      </div>
      <div class="divider"></div>
      <ul class="contacts">
        <li>
          <svg viewBox="0 0 24 24" aria-hidden="true"><path d="M6.6 10.8a15.1 15.1 0 0 0 6.6 6.6l2.2-2.2a1 1 0 0 1 1-.25 11.4 11.4 0 0 0 3.6.57 1 1 0 0 1 1 1V20a1 1 0 0 1-1 1A17 17 0 0 1 3 4a1 1 0 0 1 1-1h3.5a1 1 0 0 1 1 1c0 1.25.2 2.45.57 3.57a1 1 0 0 1-.25 1z"/></svg>
          07822254961
        </li>
        <li>
          <svg viewBox="0 0 24 24" aria-hidden="true"><path d="M2 5h20v14H2z"/><path d="M3 6l9 7 9-7" fill="#0c0c0c"/></svg>
          info@renwick-tolliver.co.uk
        </li>
        <li>
          <svg viewBox="0 0 24 24" aria-hidden="true"><circle cx="12" cy="12" r="10"/><path d="M2 12h20M12 2c3 3 3 17 0 20M12 2c-3 3-3 17 0 20" stroke="#0c0c0c" stroke-width="1.6" fill="none"/></svg>
          www.renwick-tolliver.co.uk
        </li>
      </ul>
    </div>

    <div class="address-band">14 Harrow Lane, Kettering, NN15 6QT</div>
    <div class="address-rule"></div>
  </section>

</main>
</body>
</html>
```